Quorva - corporate Business Card

We need a good look and innovative business card for a new start up company based in Los Angeles called "Quorva". We are in a payment business, including payment card, app, and ewallet. We are expert in online payment and Card not present (CNP) transaction.
We need an innovative, modern business card.

Our logo font is Aero Matics

Target Market(s)

Startup - Bank - Online Payment - Card Manufacturing

Industry/Entity Type

Startup

Contact Information for Business Card

phone: 555 014 7396 - Address: 4172 Marlowe blvd, Halden Park, OR 97299

Requirements
Must have
• Message: innovative, professional, expert, high tech, trust, online payment expert, security
Nice to have
• no comment
Should not have
• no Comment

```html
<!DOCTYPE html>
<html lang="en">
<head>
<meta charset="utf-8">
<title>Quorva – Business Card</title>
<link rel="stylesheet" href="https://fonts.googleapis.com/css2?family=Exo+2:wght@600&family=Open+Sans:wght@400;700&display=swap">
<style>
  :root {
    --page-bg: #d9d4ce;
    --card-bg: #f2eee9;
    --brand-red: #8e1a22;
    --brand-red-deep: #6f0f16;
    --band-grey: #4b4a4a;
    --band-text: #e9e6e2;
    --info-text: #f3e4e4;
  }
  html, body {
    margin: 0;
    width: 1200px;
    height: 970px;
    overflow: hidden;
    background: var(--page-bg);
  }
  .card {
    position: absolute;
    left: 80px;
    top: 189px;
    width: 1040px;
    height: 592px;
    background: var(--card-bg);
    overflow: hidden;
    box-shadow: 0 10px 30px rgba(0,0,0,0.18);
    font-family: "Open Sans", sans-serif;
  }
  .brand {
    position: absolute;
    left: 57px;
    top: 58px;
    display: flex;
    align-items: center;
    gap: 22px;
  }
  .brand-dot {
    width: 176px;
    height: 176px;
    border-radius: 50%;
    background: var(--brand-red);
  }
  .brand-name {
    font-family: "Exo 2", sans-serif;
    font-weight: 600;
    font-size: 118px;
    line-height: 1;
    color: var(--brand-red-deep);
    margin-top: -14px;
  }
  .name-band {
    position: absolute;
    left: 0;
    top: 305px;
    width: 780px;
    height: 55px;
    background: var(--band-grey);
    clip-path: polygon(0 0, 100% 0, 96% 100%, 0 100%);
    display: flex;
    align-items: center;
    padding-left: 55px;
    box-sizing: border-box;
    color: var(--band-text);
  }
  .person-name {
    font-weight: 700;
    font-size: 33px;
    padding-right: 10px;
    border-right: 2px solid var(--band-text);
    line-height: 1.1;
  }
  .person-role {
    font-size: 28px;
    padding-left: 10px;
  }
  .info-panel {
    position: absolute;
    left: 0;
    top: 360px;
    width: 100%;
    height: 232px;
    background: linear-gradient(90deg, #a3232c 0%, #8c1820 55%, #6e1016 100%);
  }
  .contact {
    position: absolute;
    left: 55px;
    top: 30px;
    color: var(--info-text);
    font-size: 27px;
    line-height: 33px;
  }
  .address { margin: 0 0 18px; }
  .contact-line {
    display: flex;
    align-items: center;
    gap: 8px;
    margin: 0;
  }
  .contact-line svg { width: 30px; height: 26px; flex: none; }
  .emblem {
    position: absolute;
    left: 715px;
    top: 265px;
    width: 340px;
    height: 340px;
    border-radius: 50%;
    background: var(--card-bg);
  }
  .emblem::after {
    content: "";
    position: absolute;
    inset: 12px;
    border-radius: 50%;
    background: var(--brand-red-deep);
  }
</style>
</head>
<body>
  <div class="card">
    <div class="brand">
      <div class="brand-dot"></div>
      <div class="brand-name">quorva</div>
    </div>

    <div class="info-panel">
      <div class="contact">
        <p class="address">4172 Marlowe blvd,<br>Halden Park, OR 97299</p>
        <p class="contact-line">
          <svg viewBox="0 0 30 26" aria-hidden="true"><rect x="1" y="1" width="28" height="24" rx="2" fill="#f3e4e4"/><path d="M7 9c0-3 16-3 16 0v2h-4V9h-8v2H7z" fill="#8e1a22"/><rect x="9" y="13" width="12" height="8" rx="1" fill="#8e1a22"/></svg>
          555 014 7396
        </p>
        <p class="contact-line">
          <svg viewBox="0 0 30 26" aria-hidden="true"><rect x="1" y="1" width="28" height="24" fill="#f3e4e4"/><path d="M4 5l11 10 11-10M4 21l8-8M26 21l-8-8" stroke="#8e1a22" stroke-width="2" fill="none"/></svg>
          hello@quorvamail.com
        </p>
      </div>
    </div>

    <div class="name-band">
      <span class="person-name">Daniel Reyes</span>
      <span class="person-role">Managing Director</span>
    </div>

    <div class="emblem"></div>
  </div>
</body>
</html>
```